Bry7Legal Letterhead

Need a new letterhead for my law firm.
IDENTIFYING INFORMATION BELOW:
Anselmo R Quintara III
Attorney at Law
Address: 2847 Larkspur Blvd, Ste 300, Dallas, TX 75204
Phone: 877-482-6017
Fax: 469-738-1452
Email: bry@bry7legal.example
Website: www.bry7legal.example

Colors
0054AA
0677BA
7BADD7
CADEEF
E8F1F8

Requirements
Must have
• Logo needs to be on the letterhead, along with identifying information which is included in the project description.

```html
<!DOCTYPE html>
<html lang="en">
<head>
<meta charset="utf-8">
<title>Bry7Legal Letterhead</title>
<link href="https://fonts.googleapis.com/css2?family=Open+Sans:wght@400;700;800&display=swap" rel="stylesheet">
<style>
  :root {
    --backdrop: #d9dcde;
    --paper: #ffffff;
    --ink: #111111;
    --brand-blue: #0677ba;
    --muted: #555555;
  }
  html, body {
    margin: 0;
    width: 1200px;
    height: 784px;
    overflow: hidden;
    background: var(--backdrop);
    font-family: "Open Sans", Arial, sans-serif;
  }
  .letterhead {
    position: absolute;
    left: 315px;
    top: 22px;
    width: 570px;
    height: 740px;
    background: var(--paper);
    box-shadow: 0 6px 18px rgba(0,0,0,0.18);
    overflow: hidden;
  }
  .header-bar-black {
    position: absolute;
    left: 0; top: 24px;
    width: 150px; height: 14px;
    background: var(--ink);
  }
  .header-bar-blue {
    position: absolute;
    right: 0; top: 62px;
    width: 150px; height: 11px;
    background: var(--brand-blue);
  }
  .brand {
    position: absolute;
    left: 160px; top: 16px;
    width: 255px;
  }
  .brand-name {
    font-weight: 800;
    font-size: 36px;
    letter-spacing: 1px;
    line-height: 1;
    color: var(--ink);
    margin: 0;
  }
  .brand-tagline {
    font-weight: 400;
    font-size: 11.5px;
    letter-spacing: 1.6px;
    color: var(--ink);
    margin: 5px 0 0 2px;
  }
  .contact-row {
    position: absolute;
    left: 14px; top: 652px;
    display: flex;
    gap: 9px;
    font-size: 8.3px;
    color: var(--muted);
    white-space: nowrap;
  }
  .contact-item { display: flex; align-items: center; gap: 3px; }
  .contact-item svg { width: 8px; height: 8px; fill: var(--ink); }
  .footer-stripes {
    position: absolute;
    left: 0; top: 664px;
    width: 570px; height: 76px;
  }
  .signatory {
    position: absolute;
    right: 18px; top: 672px;
    text-align: right;
  }
  .signatory-name {
    margin: 0;
    font-weight: 700;
    font-size: 10.5px;
    color: var(--ink);
    letter-spacing: 0.3px;
  }
  .signatory-title {
    margin: 1px 0 0;
    font-size: 8.5px;
    color: var(--ink);
    letter-spacing: 0.5px;
  }
  .website {
    position: absolute;
    right: 18px; bottom: 8px;
    font-weight: 700;
    font-size: 14px;
    color: var(--paper);
    margin: 0;
  }
</style>
</head>
<body>
<main class="letterhead">
  <div class="header-bar-black"></div>
  <div class="brand">
    <h1 class="brand-name">BRY7LEGAL</h1>
    <p class="brand-tagline">STRAIGHT TO THE POINT</p>
  </div>
  <div class="header-bar-blue"></div>

  <div class="contact-row">
    <span class="contact-item">
      <svg viewBox="0 0 10 10"><path d="M5 0a3.5 3.5 0 0 0-3.5 3.5C1.5 6 5 10 5 10s3.5-4 3.5-6.5A3.5 3.5 0 0 0 5 0zm0 5a1.4 1.4 0 1 1 0-2.8A1.4 1.4 0 0 1 5 5z"/></svg>
      2847 Larkspur Blvd, Ste 300, Dallas, TX 75204
    </span>
    <span class="contact-item">
      <svg viewBox="0 0 10 10"><path d="M2 0h2l1 2.5-1.3 1a6 6 0 0 0 2.8 2.8l1-1.3L10 6v2a2 2 0 0 1-2 2A8 8 0 0 1 0 2a2 2 0 0 1 2-2z"/></svg>
      877-482-6017
    </span>
    <span class="contact-item">
      <svg viewBox="0 0 10 10"><path d="M2.5 0h5v3h-5zM0 3.5h10V8H8v2H2V8H0zm3 3.5v2h4V7z"/></svg>
      469-738-1452
    </span>
    <span class="contact-item">
      <svg viewBox="0 0 10 10"><path d="M0 1.5h10v7H0zm1 1v.4L5 5.6l4-2.7v-.4z"/></svg>
      bry@bry7legal.example
    </span>
  </div>

  <svg class="footer-stripes" viewBox="0 0 570 76" aria-hidden="true">
    <rect x="0" y="4" width="104" height="3.5" fill="#0677ba"/>
    <rect x="110" y="10" width="126" height="3.5" fill="#111111"/>
    <rect x="242" y="4" width="88" height="3.5" fill="#0677ba"/>
    <rect x="0" y="70" width="346" height="6" fill="#111111"/>
    <polygon points="346,76 366,46 570,46 570,76" fill="#111111"/>
  </svg>

  <div class="signatory">
    <p class="signatory-name">ANSELMO R QUINTARA III</p>
    <p class="signatory-title">ATTORNEY AT LAW</p>
  </div>
  <p class="website">www.bry7legal.example</p>
</main>
</body>
</html>
```